Delia Marsh Catalog to submit to vendors

We need a catalog made with all of the products in our shop for sales purposes. Our Website is www.deliamarshandcompany.example
Almost all of our products are listed on the website. If you can not take the pictures from the site I can upload them. The descriptions are listed as well. There are three additional products that I will upload. This Catalog will be mailed to stores and should include MSRP Prices.
Updates

Hello There-We are looking for a sales catalog to send to stores in our area. We would like to include MSRP and the end we can add wholesale pricing with minimum orders. Our website is www.deliamarshandcompany.example. There are a few products that haven't been added to the website yet. Where can I upload them and send descriptions?Thank you,Colette Added Thursday, January 21, 2016

Target Market(s)

boutiques and gift shops

Industry/Entity Type

Shop

Font styles to use
Serif
Other font styles liked:
• Noteworthy

Colors
e34297
a64599
6b449b
0255a3

Requirements
Must have
• Color! I would like to organize the catalog by sections. Our premade section and our DIY kits. Maybe we should include Gift sets and put the baskets and gift boxes in one section

```html
<!DOCTYPE html>
<html lang="en">
<head>
<meta charset="utf-8">
<title>Delia Marsh Catalog — Gift Collection Spread</title>
<link rel="stylesheet" href="https://fonts.googleapis.com/css2?family=Delius&family=Dosis:wght@400;500;600&display=swap">
<style>
  :root {
    --pink: #e34297;
    --orchid: #a64599;
    --purple: #6b449b;
    --blue: #0255a3;
    --backdrop: #e9e7ee;
    --paper: #ffffff;
    --ink: #3f3a48;
    --photo-warm: #b58a7a;
    --photo-soft: #d9c9cf;
  }
  * { box-sizing: border-box; margin: 0; padding: 0; }
  html, body { width: 1200px; height: 1000px; overflow: hidden; }
  body { background: var(--backdrop); position: relative; font-family: "Dosis", sans-serif; }

  .spread {
    position: absolute; left: 10px; top: 250px; width: 1178px; height: 415px;
    box-shadow: 0 3px 10px rgba(60, 40, 80, .25);
    display: flex;
  }

  /* Left page */
  .page-left { position: relative; width: 589px; height: 100%; }
  .cover-photo {
    position: absolute; inset: 0 0 70px 0;
    background: linear-gradient(100deg, #8e5a66 0%, var(--photo-warm) 35%, var(--photo-soft) 60%, #8a6a5e 100%);
  }
  .contents {
    position: absolute; left: 100px; top: 18px; width: 390px; height: 307px;
    background: rgba(255, 255, 255, .72); border-radius: 18px;
    padding: 17px 66px 0 25px;
  }
  .contents h3 {
    font-weight: 500; font-size: 14.5px; color: var(--purple); letter-spacing: .3px;
    border-bottom: 1px solid var(--purple); padding: 0 0 0 8px; line-height: 16px;
  }
  .contents ul { list-style: none; margin-top: 2px; }
  .contents li {
    font-size: 13.5px; line-height: 17.4px; color: var(--ink); letter-spacing: .2px;
    display: flex; align-items: baseline; white-space: nowrap;
  }
  .contents li::after {
    content: ""; flex: 1; border-bottom: 1px dotted var(--ink); margin-left: 2px;
  }
  .contents .section-diy { margin-top: 19px; }
  .contents .section-sets { margin-top: 2px; }
  .tagline-band {
    position: absolute; left: 0; right: 0; bottom: 0; height: 70px;
    background: var(--pink);
    display: flex; align-items: center; justify-content: center;
    font-family: "Delius", cursive; color: #fff; font-size: 25px;
  }

  /* Right page */
  .page-right { position: relative; width: 589px; height: 100%; background: var(--paper); }
  .title-bubble { position: absolute; left: 22px; top: 18px; }
  .title-bubble .title {
    position: absolute; left: 0; top: 0; width: 556px; height: 48px;
    display: flex; align-items: center; justify-content: center;
    font-family: "Delius", cursive; font-size: 32px; font-weight: 400; color: #fff;
  }
  .title-bubble .page-no {
    position: absolute; left: 514px; top: 12px; font-family: "Dosis", sans-serif;
    font-size: 17px; color: #fff;
  }
  .frame {
    position: absolute; border: 6px solid var(--purple); border-radius: 18px;
    overflow: hidden; background: var(--purple);
  }
  .frame .shot { width: 100%; height: 100%; border-radius: 12px; }
  .frame-basket { left: 32px; top: 80px; width: 298px; height: 224px; }
  .frame-basket .shot { background: linear-gradient(180deg, #f3eef2 0%, #ece6ea 50%, #e04a9a 75%, #d63c8e 100%); }
  .frame-flowers { left: 305px; top: 85px; width: 167px; height: 125px; }
  .frame-flowers .shot { background: linear-gradient(135deg, #e7c9e6, #f1eac4 50%, #c7b3e8); }
  .frame-hearts { left: 398px; top: 148px; width: 166px; height: 126px; }
  .frame-hearts .shot { background: linear-gradient(135deg, #c8b3e6, #bde3e8 50%, #f0e6a8); }
  .frame-box { left: 340px; top: 250px; width: 166px; height: 127px; }
  .frame-box .shot { background: linear-gradient(180deg, #f2f0f2 0%, #ece8ec 50%, #e2468f 100%); }
  .product-label {
    position: absolute; left: 90px; top: 315px; width: 180px; text-align: center;
  }
  .product-label .name { font-size: 21px; font-weight: 500; color: var(--pink); letter-spacing: .5px; line-height: 24px; }
  .product-label .price { font-size: 19px; font-weight: 500; color: var(--purple); line-height: 24px; }
  .foot-band { position: absolute; left: 0; right: 0; bottom: 0; height: 22px; background: var(--purple); }
</style>
</head>
<body>
  <div class="spread">
    <section class="page-left">
      <div class="cover-photo" role="img" aria-label="Photo of three girls laughing around a table with a pink gift basket of bath products"></div>
      <nav class="contents">
        <h3>PRE-MADE COLLECTION</h3>
        <ul>
          <li>HOLIDAY COLLECTION</li>
          <li>BATH BOMBS</li>
          <li>LIP BALMS</li>
          <li>BODY BUTTER</li>
          <li>BODY LOTION</li>
          <li>BODY WASH</li>
          <li>METEOR BATH BOMB W/ SURPRISE INSIDE</li>
          <li>SHEA BUTTER HEART SOAPS</li>
          <li>ANTI-BACTERIAL HAND GEL</li>
          <li>ALL-NATURAL BUG SPRAY</li>
          <li>MANI-PEDI SPA BASKET</li>
        </ul>
        <h3 class="section-diy">DO IT YOURSELF</h3>
        <h3 class="section-sets">GIFT SET AND BOXES</h3>
      </nav>
      <div class="tagline-band">Be Bright. Be Playful. Be Thankful.</div>
    </section>

    <section class="page-right">
      <div class="title-bubble">
        <svg width="548" height="62" viewBox="0 0 548 62" aria-hidden="true">
          <path d="M24 0 H522 A24 24 0 0 1 546 24 A24 24 0 0 1 530 46 L540 58 L518 48 H24 A24 24 0 0 1 24 0 Z" fill="var(--purple)"/>
        </svg>
        <h2 class="title">Gift Collection</h2>
        <span class="page-no">2</span>
      </div>

      <div class="frame frame-basket"><div class="shot" role="img" aria-label="Photo of a pink gift basket with lotion, body butter jar, soap and bath bomb"></div></div>
      <div class="frame frame-flowers"><div class="shot" role="img" aria-label="Photo of a box of pastel flower-shaped bath bombs"></div></div>
      <div class="frame frame-hearts"><div class="shot" role="img" aria-label="Photo of a box of pastel heart-shaped soaps"></div></div>
      <div class="frame frame-box"><div class="shot" role="img" aria-label="Photo of a small pink gift box with heart soaps and a ribbon"></div></div>

      <div class="product-label">
        <div class="name">GIFT BASKET</div>
        <div class="price">from $25.00</div>
      </div>

      <div class="foot-band"></div>
    </section>
  </div>
</body>
</html>
```